Up to the Challenge - PPT Template with Splash Slide

We are looking for a PPT template that has 4 slides.
1. Splash slide (Creative, fun, no content, a visual representation of the theme)
2. Section header slide
3. Content Slide
4. Content Slide, another design option
The theme is 'UP to the Challenge'. The design should reflect this theme.
The colors should be in Purple (#864B99), Blue (#0A80C2), and Green (#52B054).

```html
<!DOCTYPE html>
<html lang="en">
<head>
<meta charset="utf-8">
<title>Up to the Challenge – Slide Template Overview</title>
<link rel="stylesheet" href="https://fonts.googleapis.com/css2?family=Rubik:wght@800;900&family=Saira+Condensed:ital,wght@1,800&family=Open+Sans:wght@400;700&display=swap">
<style>
  :root{
    --canvas:#ffffff;
    --ink:#222222;
    --green:#3fa64a;
    --green-deep:#0c6e45;
    --green-bg:#0b6a14;
    --purple:#86208a;
    --purple-mid:#864b99;
    --purple-soft:#e0b6ea;
    --black:#060606;
    --muted:#9a9a9a;
  }
  html,body{margin:0;padding:0;overflow:hidden;}
  body{width:1042px;height:1200px;background:var(--canvas);position:relative;font-family:"Open Sans",Arial,sans-serif;}
  .defs{position:absolute;width:0;height:0;}
  .slide{position:absolute;width:236px;height:133px;box-shadow:0 3px 8px rgba(0,0,0,.22);display:block;}
  .c1{left:19px}.c2{left:275px}.c3{left:531px}.c4{left:787px}
  .r1{top:198px}.r2{top:366px}.r3{top:534px}.r4{top:702px}.r5{top:869px}
  .splash-title{font-family:"Saira Condensed","Arial Narrow",sans-serif;font-style:italic;font-weight:800;text-anchor:middle;}
  .hero-title{font-family:"Saira Condensed","Arial Narrow",sans-serif;font-style:italic;font-weight:800;text-anchor:middle;font-size:60px;}
  .kicker{font-family:"Open Sans",Arial,sans-serif;font-weight:700;font-size:4.2px;fill:var(--ink);}
  .heading{font-family:"Rubik",Arial,sans-serif;font-weight:900;font-size:17px;fill:var(--green);}
  .heading .last{fill:var(--green-deep);}
  .break-title{font-family:"Rubik",Arial,sans-serif;font-weight:900;font-size:17px;fill:var(--green-deep);}
  .break-title.purple{fill:var(--purple-mid);}
  .body-copy{font-family:"Open Sans",Arial,sans-serif;font-size:4.3px;fill:#444;}
  .body-copy .lead{font-weight:700;fill:var(--ink);}
  .foot{font-family:"Open Sans",Arial,sans-serif;font-size:4px;fill:var(--muted);}
</style>
</head>
<body>

<svg class="defs" aria-hidden="true">
  <defs>
    <linearGradient id="chess" x1="0" y1="0" x2="0" y2="1">
      <stop offset="0" stop-color="#d9cfae" stop-opacity="0"/>
      <stop offset=".35" stop-color="#cfc4a0"/>
      <stop offset="1" stop-color="#e6e2d6"/>
    </linearGradient>
    <linearGradient id="chessSolid" x1="0" y1="0" x2="0" y2="1">
      <stop offset="0" stop-color="#3a362c"/>
      <stop offset=".5" stop-color="#cfc4a0"/>
      <stop offset="1" stop-color="#e8e4d8"/>
    </linearGradient>
    <linearGradient id="skyPurple" x1="0" y1="0" x2="0" y2="1">
      <stop offset="0" stop-color="#b26cc4"/>
      <stop offset="1" stop-color="#eccdf2"/>
    </linearGradient>
    <linearGradient id="sunset" x1="0" y1="0" x2="0" y2="1">
      <stop offset="0" stop-color="#a8782c"/>
      <stop offset=".5" stop-color="#e8a24a"/>
      <stop offset="1" stop-color="#d27a1e"/>
    </linearGradient>
    <linearGradient id="snowSky" x1="0" y1="0" x2="0" y2="1">
      <stop offset="0" stop-color="#3d5966"/>
      <stop offset=".55" stop-color="#a9bcc6"/>
      <stop offset="1" stop-color="#8a5a48"/>
    </linearGradient>
    <linearGradient id="monoSplash" x1="0" y1="0" x2="1" y2="1">
      <stop offset="0" stop-color="#3c3c3c"/>
      <stop offset=".6" stop-color="#b8b8b8"/>
      <stop offset="1" stop-color="#eeeeee"/>
    </linearGradient>
    <linearGradient id="moto" x1="0" y1="0" x2="1" y2="1">
      <stop offset="0" stop-color="#7f8f86"/>
      <stop offset=".5" stop-color="#2f4f86"/>
      <stop offset="1" stop-color="#d8dcd6"/>
    </linearGradient>
    <linearGradient id="chessBlue" x1="0" y1="0" x2="0" y2="1">
      <stop offset="0" stop-color="#3d5a8e"/>
      <stop offset=".6" stop-color="#1c2d58"/>
      <stop offset="1" stop-color="#b4323a"/>
    </linearGradient>
    <linearGradient id="band" x1="0" y1="0" x2="1" y2="1">
      <stop offset="0" stop-color="#86208a"/>
      <stop offset=".55" stop-color="#2d8a58"/>
      <stop offset="1" stop-color="#0b5f6e"/>
    </linearGradient>
    <linearGradient id="bandGreen" x1="0" y1="0" x2="1" y2="0">
      <stop offset="0" stop-color="#3fae49"/>
      <stop offset="1" stop-color="#0c6e45"/>
    </linearGradient>
  </defs>
</svg>

<!-- Row 1: splash variants -->
<svg class="slide c1 r1" viewBox="0 0 400 225">
  <rect width="400" height="225" fill="var(--black)"/>
  <rect y="70" width="400" height="155" fill="url(#chess)" role="img" aria-label="Glass chess pieces on a board"/>
  <text class="splash-title" x="205" y="53" font-size="34" fill="#fff">UP TO THE</text>
  <text class="splash-title" x="205" y="93" font-size="34" fill="#fff">CHALLENGE</text>
  <g class="foot"><text x="30" y="216">Up to the Challenge presentation</text><text x="180" y="216">All Rights Reserved</text><text x="368" y="216">2</text></g>
</svg>

<svg class="slide c2 r1" viewBox="0 0 400 225">
  <rect width="400" height="225" fill="var(--green-bg)"/>
  <rect y="70" width="400" height="155" fill="url(#chess)" role="img" aria-label="Glass chess pieces on a board"/>
  <text class="splash-title" x="205" y="53" font-size="34" fill="#fff">UP TO THE</text>
  <text class="splash-title" x="205" y="93" font-size="34" fill="#fff">CHALLENGE</text>
  <g class="foot"><text x="30" y="216">Up to the Challenge presentation</text><text x="180" y="216">All Rights Reserved</text><text x="368" y="216">3</text></g>
</svg>

<svg class="slide c3 r1" viewBox="0 0 400 225">
  <rect width="400" height="225" fill="var(--purple)"/>
  <rect y="70" width="400" height="155" fill="url(#chess)" role="img" aria-label="Glass chess pieces on a board"/>
  <text class="splash-title" x="205" y="53" font-size="34" fill="#fff">UP TO THE</text>
  <text class="splash-title" x="205" y="93" font-size="34" fill="#fff">CHALLENGE</text>
  <g class="foot"><text x="30" y="216">Up to the Challenge presentation</text><text x="180" y="216">All Rights Reserved</text><text x="368" y="216">4</text></g>
</svg>

<svg class="slide c4 r1" viewBox="0 0 400 225">
  <rect width="400" height="225" fill="url(#skyPurple)" role="img" aria-label="Climber silhouette on a cliff against a purple sky"/>
  <path d="M278 0 H400 V225 H268 C272 180 262 140 270 100 C276 60 268 30 278 0Z" fill="var(--green-bg)"/>
  <text class="splash-title" x="135" y="108" font-size="28" fill="#fff" stroke="var(--purple-mid)" stroke-width=".8">UP TO THE</text>
  <text class="splash-title" x="135" y="140" font-size="28" fill="#fff" stroke="var(--purple-mid)" stroke-width=".8">CHALLENGE</text>
  <g class="foot"><text x="30" y="216">Up to the Challenge presentation</text><text x="180" y="216">All Rights Reserved</text><text x="368" y="216">1</text></g>
</svg>

<!-- Row 2: large-type splash variants -->
<svg class="slide c1 r2" viewBox="0 0 400 225">
  <rect width="400" height="225" fill="var(--black)"/>
  <rect y="60" width="400" height="165" fill="url(#chess)" role="img" aria-label="Glass chess pieces on a board"/>
  <text class="hero-title" x="205" y="98" fill="var(--purple)">UP TO THE</text>
  <text class="hero-title" x="205" y="188" fill="var(--purple-soft)">CHALLENGE</text>
  <g class="foot"><text x="30" y="216">Up to the Challenge presentation</text><text x="180" y="216">All Rights Reserved</text><text x="368" y="216">5</text></g>
</svg>

<svg class="slide c2 r2" viewBox="0 0 400 225">
  <rect width="400" height="225" fill="url(#chessBlue)" role="img" aria-label="Hand moving a chess piece on a blue-lit board"/>
  <text class="hero-title" x="205" y="98" fill="#5cb050" fill-opacity=".9">UP TO THE</text>
  <text class="hero-title" x="205" y="188" fill="#5cb050" fill-opacity=".9">CHALLENGE</text>
  <g class="foot"><text x="30" y="216">Up to the Challenge presentation</text><text x="180" y="216">All Rights Reserved</text><text x="368" y="216">6</text></g>
</svg>

<svg class="slide c3 r2" viewBox="0 0 400 225">
  <rect width="400" height="225" fill="url(#sunset)" role="img" aria-label="Climber silhouette on a cliff at sunset"/>
  <path d="M276 0 H400 V225 H268 C274 170 262 120 270 80 C276 40 268 20 276 0Z" fill="var(--black)"/>
  <text class="hero-title" x="205" y="98" fill="#fff">UP TO THE</text>
  <text class="hero-title" x="205" y="188" fill="#fff">CHALLENGE</text>
  <g class="foot"><text x="30" y="216">Up to the Challenge presentation</text><text x="180" y="216">All Rights Reserved</text><text x="368" y="216">7</text></g>
</svg>

<svg class="slide c4 r2" viewBox="0 0 400 225">
  <rect width="400" height="225" fill="url(#sunset)" role="img" aria-label="Climber silhouette on a cliff at sunset"/>
  <path d="M276 0 H400 V225 H268 C274 170 262 120 270 80 C276 40 268 20 276 0Z" fill="var(--black)"/>
  <text class="hero-title" x="205" y="98" fill="var(--purple-soft)">UP TO THE</text>
  <text class="hero-title" x="205" y="188" fill="var(--purple-soft)">CHALLENGE</text>
  <text class="hero-title" x="205" y="188" fill="var(--purple)" clip-path="inset(0 0 0 68%)">CHALLENGE</text>
  <g class="foot"><text x="30" y="216">Up to the Challenge presentation</text><text x="180" y="216">All Rights Reserved</text><text x="368" y="216">8</text></g>
</svg>

<!-- Row 3 -->
<svg class="slide c1 r3" viewBox="0 0 400 225">
  <rect width="400" height="225" fill="#fff"/>
  <path d="M0 0 H400 V0 C330 80 260 170 130 188 C70 196 30 170 0 120Z" fill="url(#monoSplash)" role="img" aria-label="Surfer carving through a wave in black and white"/>
  <path d="M400 0 C330 80 260 170 130 188 C70 196 30 170 0 120" fill="none" stroke="url(#band)" stroke-width="5"/>
  <text class="break-title" x="278" y="138">BREAK</text>
  <text class="break-title" x="278" y="162">SECTION</text>
  <text class="break-title" x="278" y="186">SLIDE</text>
  <g class="foot"><text x="30" y="216">Up to the Challenge presentation</text><text x="180" y="216">All Rights Reserved</text><text x="365" y="216">38</text></g>
</svg>

<svg class="slide c2 r3" viewBox="0 0 400 225">
  <rect width="400" height="225" fill="#fff"/>
  <path d="M232 0 H400 V225 C330 205 260 150 244 90 C236 50 238 22 232 0Z" fill="url(#moto)" role="img" aria-label="Motocross rider splashing through water"/>
  <path d="M400 225 C330 205 260 150 244 90 C236 50 238 22 232 0" fill="none" stroke="url(#band)" stroke-width="4"/>
  <text class="kicker" x="42" y="50">LOREM IPSUM IS SIMPLY DUMMY TEXT OF THE PRINTING</text>
  <text class="heading" x="42" y="72">UP TO THE</text>
  <text class="heading" x="42" y="96">CHALLENGE</text>
  <text class="heading" x="42" y="120"><tspan class="last">IMAGE RIGHT</tspan></text>
  <line x1="42" y1="128" x2="76" y2="128" stroke="var(--purple-mid)" stroke-width="1.4"/>
  <text class="body-copy" x="42" y="150"><tspan class="lead">Lorem Ipsum</tspan> is simply dummy text of the printing</text>
  <text class="body-copy" x="42" y="159">and typesetting industry. Lorem Ipsum has been the</text>
  <text class="body-copy" x="42" y="168">industry's standard dummy text ever since the 1500s,</text>
  <text class="body-copy" x="42" y="177">when an unknown printer took a galley of type and</text>
  <g class="foot"><text x="30" y="216">Up to the Challenge presentation</text><text x="180" y="216">All Rights Reserved</text></g>
</svg>

<svg class="slide c3 r3" viewBox="0 0 400 225">
  <rect width="400" height="225" fill="#fff"/>
  <path d="M190 0 H400 V225 H200 C250 170 262 70 190 0Z" fill="url(#snowSky)" role="img" aria-label="Snowboarder jumping over rocky snow slope"/>
  <path d="M190 0 C262 70 250 170 200 225" fill="none" stroke="url(#band)" stroke-width="4"/>
  <text class="kicker" x="42" y="50">LOREM IPSUM IS SIMPLY DUMMY TEXT OF THE PRINTING</text>
  <text class="heading" x="42" y="72">UP TO THE</text>
  <text class="heading" x="42" y="96">CHALLENGE</text>
  <text class="heading" x="42" y="120"><tspan class="last">IMAGE RIGHT</tspan></text>
  <line x1="42" y1="128" x2="76" y2="128" stroke="var(--purple-mid)" stroke-width="1.4"/>
  <text class="body-copy" x="42" y="150"><tspan class="lead">Lorem Ipsum</tspan> is simply dummy text of the printing</text>
  <text class="body-copy" x="42" y="159">and typesetting industry. Lorem Ipsum has been the</text>
  <text class="body-copy" x="42" y="168">industry's standard dummy text ever since the 1500s,</text>
  <text class="body-copy" x="42" y="177">when an unknown printer took a galley of type and</text>
  <g class="foot"><text x="30" y="216">Up to the Challenge presentation</text><text x="180" y="216">All Rights</text></g>
</svg>

<svg class="slide c4 r3" viewBox="0 0 400 225">
  <rect width="400" height="225" fill="#fff"/>
  <path d="M70 14 C140 0 160 30 150 80 C145 120 170 120 210 140 C240 160 220 205 160 203 C110 202 60 200 30 170 C0 140 0 30 70 14Z" fill="url(#sunset)" role="img" aria-label="Climber silhouette on a cliff at sunset"/>
  <path d="M108 10 C118 60 100 110 112 150 C120 180 110 200 112 203 L160 203 C220 205 240 160 210 140 C170 120 145 120 150 80 C160 30 140 0 108 10Z" fill="var(--black)"/>
  <path d="M30 170 C0 140 0 30 70 14 C140 0 160 30 150 80" fill="none" stroke="url(#bandGreen)" stroke-width="4"/>
  <path d="M150 80 C145 120 170 120 210 140 C240 160 220 205 160 203" fill="none" stroke="url(#band)" stroke-width="4"/>
  <text class="kicker" x="238" y="50">LOREM IPSUM IS SIMPLY DUMMY TEXT OF THE PRINTING</text>
  <text class="heading" x="238" y="72">UP TO THE</text>
  <text class="heading" x="238" y="96">CHALLENGE</text>
  <text class="heading" x="238" y="120"><tspan class="last">IMAGE LEFT</tspan></text>
  <line x1="238" y1="128" x2="272" y2="128" stroke="var(--purple-mid)" stroke-width="1.4"/>
  <text class="body-copy" x="238" y="150"><tspan class="lead">Lorem Ipsum</tspan> is simply dummy text of the printing</text>
  <text class="body-copy" x="238" y="159">and typesetting industry. Lorem Ipsum has been the</text>
  <text class="body-copy" x="238" y="168">industry's standard dummy text ever since the 1500s,</text>
  <text class="body-copy" x="238" y="177">when an unknown printer took a galley of type and</text>
  <g class="foot"><text x="30" y="216">Up to the Challenge presentation</text><text x="180" y="216">All Rights Reserved</text><text x="365" y="216">43</text></g>
</svg>

<!-- Row 4 -->
<svg class="slide c1 r4" viewBox="0 0 400 225">
  <rect width="400" height="225" fill="#fff"/>
  <path d="M0 0 H210 C160 50 150 170 210 225 H0Z" fill="url(#snowSky)" role="img" aria-label="Snowboarder jumping over rocky snow slope"/>
  <path d="M210 0 C160 50 150 170 210 225" fill="none" stroke="url(#bandGreen)" stroke-width="4"/>
  <text class="kicker" x="236" y="50">LOREM IPSUM IS SIMPLY DUMMY TEXT OF THE PRINTING</text>
  <text class="heading" x="236" y="72">UP TO THE</text>
  <text class="heading" x="236" y="96">CHALLENGE</text>
  <text class="heading" x="236" y="120"><tspan class="last">IMAGE LEFT</tspan></text>
  <line x1="236" y1="128" x2="270" y2="128" stroke="var(--purple-mid)" stroke-width="1.4"/>
  <text class="body-copy" x="236" y="150"><tspan class="lead">Lorem Ipsum</tspan> is simply dummy text of the printing</text>
  <text class="body-copy" x="236" y="159">and typesetting industry. Lorem Ipsum has been the</text>
  <text class="body-copy" x="236" y="168">industry's standard dummy text ever since the 1500s,</text>
  <text class="body-copy" x="236" y="177">when an unknown printer took a galley of type and</text>
  <g class="foot"><text x="180" y="216">All Rights Reserved</text><text x="365" y="216">41</text></g>
</svg>

<svg class="slide c2 r4" viewBox="0 0 400 225">
  <rect width="400" height="225" fill="#fff"/>
  <path d="M0 0 H210 C240 80 160 170 0 225Z" fill="url(#monoSplash)" role="img" aria-label="Surfer carving through a wave in black and white"/>
  <path d="M210 0 C240 80 160 170 0 225" fill="none" stroke="url(#band)" stroke-width="4"/>
  <text class="kicker" x="236" y="50">LOREM IPSUM IS SIMPLY DUMMY TEXT OF THE PRINTING</text>
  <text class="heading" x="236" y="72">UP TO THE</text>
  <text class="heading" x="236" y="96">CHALLENGE</text>
  <text class="heading" x="236" y="120"><tspan class="last">IMAGE LEFT</tspan></text>
  <line x1="236" y1="128" x2="270" y2="128" stroke="var(--purple-mid)" stroke-width="1.4"/>
  <text class="body-copy" x="236" y="150"><tspan class="lead">Lorem Ipsum</tspan> is simply dummy text of the printing</text>
  <text class="body-copy" x="236" y="159">and typesetting industry. Lorem Ipsum has been the</text>
  <text class="body-copy" x="236" y="168">industry's standard dummy text ever since the 1500s,</text>
  <text class="body-copy" x="236" y="177">when an unknown printer took a galley of type and</text>
  <g class="foot"><text x="30" y="216">Up to the Challenge presentation</text><text x="180" y="216">All Rights Reserved</text><text x="365" y="216">42</text></g>
</svg>

<svg class="slide c3 r4" viewBox="0 0 400 225">
  <rect width="400" height="225" fill="#fff"/>
  <path d="M320 10 C380 5 405 60 398 120 C392 180 350 205 290 200 C230 196 180 190 180 150 C180 120 230 120 245 80 C260 40 270 14 320 10Z" fill="url(#chessBlue)" role="img" aria-label="Hand moving a chess piece on a blue-lit board"/>
  <path d="M245 80 C260 40 270 14 320 10 C380 5 405 60 398 120" fill="none" stroke="url(#bandGreen)" stroke-width="4"/>
  <path d="M290 200 C230 196 180 190 180 150 C180 120 230 120 245 80" fill="none" stroke="url(#band)" stroke-width="4"/>
  <text class="kicker" x="44" y="46">LOREM IPSUM IS SIMPLY DUMMY TEXT OF THE PRINTING</text>
  <text class="heading" x="44" y="68">UP TO THE</text>
  <text class="heading" x="44" y="92">CHALLENGE</text>
  <text class="heading" x="44" y="116"><tspan class="last">IMAGE RIGHT</tspan></text>
  <line x1="44" y1="124" x2="78" y2="124" stroke="var(--purple-mid)" stroke-width="1.4"/>
  <text class="body-copy" x="44" y="146"><tspan class="lead">Lorem Ipsum</tspan> is simply dummy text of the printing</text>
  <text class="body-copy" x="44" y="155">and typesetting industry. Lorem Ipsum has been the</text>
  <text class="body-copy" x="44" y="164">industry's standard dummy text ever since the 1500s,</text>
  <text class="body-copy" x="44" y="173">when an unknown printer took a galley of type and</text>
  <g class="foot"><text x="30" y="216">Up to the Challenge presentation</text><text x="180" y="216">All Rights Reserved</text><text x="365" y="216">44</text></g>
</svg>

<svg class="slide c4 r4" viewBox="0 0 400 225">
  <rect width="400" height="225" fill="#fff"/>
  <path d="M205 0 H400 V225 H215 C185 160 180 60 205 0Z" fill="url(#monoSplash)" role="img" aria-label="Snowboarder kicking up snow in black and white"/>
  <path d="M205 0 C180 60 185 160 215 225" fill="none" stroke="url(#bandGreen)" stroke-width="5"/>
  <text class="kicker" x="44" y="46">LOREM IPSUM IS SIMPLY DUMMY TEXT OF THE PRINTING</text>
  <text class="heading" x="44" y="68">UP TO THE</text>
  <text class="heading" x="44" y="92">CHALLENGE</text>
  <text class="heading" x="44" y="116"><tspan class="last">IMAGE RIGHT</tspan></text>
  <line x1="44" y1="124" x2="78" y2="124" stroke="var(--purple-mid)" stroke-width="1.4"/>
  <text class="body-copy" x="44" y="146"><tspan class="lead">Lorem Ipsum</tspan> is simply dummy text of the printing</text>
  <text class="body-copy" x="44" y="155">and typesetting industry. Lorem Ipsum has been the</text>
  <text class="body-copy" x="44" y="164">industry's standard dummy text ever since the 1500s,</text>
  <text class="body-copy" x="44" y="173">when an unknown printer took a galley of type and</text>
  <g class="foot"><text x="30" y="216">Up to the Challenge presentation</text><text x="180" y="216">All Rights Reserved</text></g>
</svg>

<!-- Row 5 -->
<svg class="slide c1 r5" viewBox="0 0 400 225">
  <rect width="400" height="225" fill="#fff"/>
  <path d="M0 0 H140 C100 70 110 170 200 225 H0Z" fill="url(#moto)" role="img" aria-label="Motocross rider splashing through water"/>
  <path d="M140 0 C100 70 110 170 200 225" fill="none" stroke="url(#band)" stroke-width="5"/>
  <text class="kicker" x="232" y="50">LOREM IPSUM IS SIMPLY DUMMY TEXT OF THE PRINTING</text>
  <text class="heading" x="232" y="72">UP TO THE</text>
  <text class="heading" x="232" y="96">CHALLENGE</text>
  <text class="heading" x="232" y="120"><tspan class="last">IMAGE LEFT</tspan></text>
  <line x1="232" y1="128" x2="266" y2="128" stroke="var(--purple-mid)" stroke-width="1.4"/>
  <text class="body-copy" x="232" y="150"><tspan class="lead">Lorem Ipsum</tspan> is simply dummy text of the printing</text>
  <text class="body-copy" x="232" y="159">and typesetting industry. Lorem Ipsum has been the</text>
  <text class="body-copy" x="232" y="168">industry's standard dummy text ever since the 1500s,</text>
  <text class="body-copy" x="232" y="177">when an unknown printer took a galley of type and</text>
  <g class="foot"><text x="180" y="216">All Rights Reserved</text><text x="365" y="216">46</text></g>
</svg>

<svg class="slide c2 r5" viewBox="0 0 400 225">
  <rect width="400" height="225" fill="#fff"/>
  <path d="M0 225 C30 160 110 115 210 108 C310 100 370 70 400 0 V225Z" fill="url(#chessSolid)" role="img" aria-label="Glass chess pieces on a board"/>
  <path d="M0 225 C30 160 110 115 210 108 C310 100 370 70 400 0" fill="none" stroke="url(#band)" stroke-width="4"/>
  <text class="kicker" x="36" y="30">LOREM IPSUM IS SIMPLY DUMMY TEXT OF THE PRINTING</text>
  <text class="heading" x="36" y="52">UP TO THE</text>
  <text class="heading" x="36" y="76">CHALLENGE</text>
  <text class="body-copy" x="178" y="31"><tspan class="lead">Lorem Ipsum</tspan> is simply dummy text of the printing and typesetting industry</text>
  <text class="body-copy" x="178" y="40">Lorem Ipsum has been the industry's standard dummy text ever since the</text>
  <text class="body-copy" x="178" y="49">1500s, when an unknown printer took a galley of type and. Lorem Ipsum is</text>
  <text class="body-copy" x="178" y="58">simply dummy text of the printing and typesetting industry. Lorem Ipsum</text>
  <text class="body-copy" x="178" y="67">has been the industry's standard dummy text ever since the 1500s, when an</text>
  <text class="body-copy" x="178" y="76">unknown printer took a galley of type</text>
</svg>

<svg class="slide c3 r5" viewBox="0 0 400 225">
  <rect width="400" height="225" fill="#fff"/>
  <path d="M0 100 C90 108 150 82 210 62 C290 38 340 30 400 22 V225 H0Z" fill="url(#snowSky)" role="img" aria-label="Snowboarder jumping over rocky snow slope"/>
  <path d="M0 100 C90 108 150 82 210 62 C290 38 340 30 400 22" fill="none" stroke="url(#band)" stroke-width="4"/>
  <text class="break-title purple" x="57" y="30">BREAK</text>
  <text class="break-title purple" x="57" y="54">SECTION</text>
  <text class="break-title purple" x="57" y="78">SLIDE</text>
  <g class="foot" style="fill:#eee"><text x="180" y="216">All Rights Reserved</text></g>
</svg>

<svg class="slide c4 r5" viewBox="0 0 400 225">
  <rect width="400" height="225" fill="#fff"/>
  <path d="M0 0 H400 C280 15 215 50 195 95 C150 140 70 165 0 140Z" fill="url(#snowSky)" role="img" aria-label="Snowboarder jumping over rocky snow slope"/>
  <path d="M0 140 C70 165 150 140 195 95 C215 50 280 15 400 0" fill="none" stroke="url(#bandGreen)" stroke-width="7"/>
  <text class="kicker" x="246" y="65">LOREM IPSUM IS SIMPLY DUMMY TEXT OF THE PRINTING</text>
  <text class="heading" x="246" y="87">UP TO THE</text>
  <text class="heading" x="246" y="111">CHALLENGE</text>
  <text class="heading" x="246" y="135"><tspan class="last">IMAGE LEFT</tspan></text>
  <line x1="246" y1="143" x2="280" y2="143" stroke="var(--purple-mid)" stroke-width="1.4"/>
  <text class="body-copy" x="246" y="163"><tspan class="lead">Lorem Ipsum</tspan> is simply dummy text of the printing</text>
  <text class="body-copy" x="246" y="172">and typesetting industry. Lorem Ipsum has been the</text>
  <text class="body-copy" x="246" y="181">industry's standard dummy text ever since the 1500s,</text>
  <text class="body-copy" x="246" y="190">when an unknown printer took a galley of type and</text>
  <g class="foot"><text x="30" y="216">Up to the Challenge presentation</text><text x="180" y="216">All Rights Reserved</text><text x="365" y="216">49</text></g>
</svg>

</body>
</html>
```